My project benefits Military, First Responders, Police, Fire, and Educators.

Contact Information for Business Card

2 Sided appointment card. Visual side will have my head shot with "Brisk Lantern" in a bold graffic/text. I am picturing maybe the headshot applied to a filter that has a matrix effect where the picture is made up of data/numbers flowing vertically through the photo. I am of course open to other concepts as well. Side two will have contact info presented in an attractive visual complimenting the front.

```html
<!DOCTYPE html>
<html lang="en">
<head>
<meta charset="utf-8">
<title>Brisk Lantern – Appointment Card</title>
<link rel="stylesheet" href="https://fonts.googleapis.com/css2?family=PT+Sans:wght@400;700&display=swap">
<style>
  :root {
    --brand-blue: #1458a8;
    --brand-teal: #2bb08c;
    --paper: #ffffff;
    --backdrop: #e9ebee;
    --rule: rgba(255, 255, 255, 0.28);
    --photo-light: #c9a88f;
    --photo-mid: #8a6e5e;
    --photo-dark: #1d2740;
  }
  * { box-sizing: border-box; margin: 0; padding: 0; }
  html, body {
    width: 1200px; height: 900px; overflow: hidden;
    background: var(--backdrop);
    font-family: "PT Sans", "Helvetica Neue", Arial, sans-serif;
  }
  .canvas { position: relative; width: 1200px; height: 900px; }
  .card {
    position: absolute; overflow: hidden; background: var(--paper);
    box-shadow: 0 6px 18px rgba(0, 0, 0, 0.18);
  }

  /* Front side */
  .card-front { left: 78px; top: 34px; width: 588px; height: 364px; }
  .front-band {
    position: absolute; left: 0; top: 182px; width: 100%; height: 182px;
    background: var(--brand-blue);
  }
  .wordmark {
    position: absolute; left: 32px; top: 78px;
    display: flex; align-items: center; gap: 12px;
    color: var(--brand-blue); font-weight: 700; font-size: 38px; letter-spacing: -0.5px;
  }
  .wordmark-dot {
    width: 16px; height: 16px; border-radius: 50%; background: var(--brand-blue);
  }
  .headshot {
    position: absolute; left: 298px; top: 0; width: 290px; height: 364px;
    background: linear-gradient(180deg, var(--photo-light) 0%, var(--photo-mid) 50%, var(--photo-dark) 72%, var(--photo-dark) 100%);
  }
  .person { position: absolute; left: 30px; top: 197px; color: #fff; }
  .person-name { font-size: 20px; font-weight: 700; line-height: 1.1; }
  .person-title { font-size: 16px; line-height: 1.4; }
  .contact-list { position: absolute; left: 0; top: 256px; width: 247px; list-style: none; }
  .contact-item {
    display: flex; align-items: center; gap: 12px;
    height: 31px; padding-left: 34px;
    color: #fff; font-size: 16px;
  }
  .contact-item + .contact-item { border-top: 1px solid var(--rule); }
  .contact-item svg { width: 12px; height: 12px; flex: none; fill: #fff; }

  /* Back side */
  .card-back { left: 388px; top: 505px; width: 567px; height: 352px; }
  .back-band { position: absolute; left: 0; width: 100%; background: var(--brand-blue); }
  .back-band.top { top: 0; height: 100px; }
  .back-band.bottom { bottom: 0; height: 65px; }
  .appointment-title {
    position: absolute; top: 113px; width: 100%; text-align: center;
    color: var(--brand-teal); font-size: 20px; font-weight: 700;
  }
  .field {
    position: absolute; left: 98px; display: flex; align-items: flex-end;
    color: var(--brand-blue); font-size: 15px;
  }
  .field-line {
    display: inline-block; border-bottom: 2px dotted var(--brand-blue);
    margin-left: 4px; margin-bottom: 4px;
  }
  .field.name { top: 157px; }
  .field.name .field-line { width: 316px; }
  .field.date { top: 210px; }
  .field.date .field-line { width: 322px; }
  .notice {
    position: absolute; top: 256px; width: 100%; text-align: center;
    color: var(--brand-teal); font-size: 15px; font-weight: 700;
  }
</style>
</head>
<body>
<main class="canvas">

  <section class="card card-front" aria-label="Card front">
    <div class="front-band"></div>
    <div class="wordmark"><span class="wordmark-dot"></span>Brisk Lantern</div>
    <div class="headshot" role="img" aria-label="Headshot of the managing director in a dark suit and striped tie"></div>
    <div class="person">
      <p class="person-name">Daniel Harwick</p>
      <p class="person-title">Managing Director</p>
    </div>
    <ul class="contact-list">
      <li class="contact-item">
        <svg viewBox="0 0 24 24" aria-hidden="true"><path d="M6.6 10.8a15.1 15.1 0 0 0 6.6 6.6l2.2-2.2a1 1 0 0 1 1-.25 11.4 11.4 0 0 0 3.6.57 1 1 0 0 1 1 1V20a1 1 0 0 1-1 1A17 17 0 0 1 3 4a1 1 0 0 1 1-1h3.5a1 1 0 0 1 1 1c0 1.25.2 2.45.57 3.57a1 1 0 0 1-.25 1z"/></svg>
        044-555 210 347
      </li>
      <li class="contact-item">
        <svg viewBox="0 0 24 24" aria-hidden="true"><path d="M2 5h20v14H2z M4 7v.4l8 5 8-5V7l-8 5z" fill-rule="evenodd"/></svg>
        hello@brisklantern.com
      </li>
      <li class="contact-item">
        <svg viewBox="0 0 24 24" aria-hidden="true"><path d="M10.6 13.4a1 1 0 0 1 0-1.4l3.5-3.5a1 1 0 1 1 1.4 1.4L12 13.4a1 1 0 0 1-1.4 0zM8 20a4 4 0 0 1-2.8-6.8l2.5-2.5 1.4 1.4-2.5 2.5a2 2 0 0 0 2.8 2.8l2.5-2.5 1.4 1.4-2.5 2.5A4 4 0 0 1 8 20zm8.3-6.7-1.4-1.4 2.5-2.5a2 2 0 0 0-2.8-2.8l-2.5 2.5-1.4-1.4 2.5-2.5a4 4 0 0 1 5.6 5.6z"/></svg>
        www.brisklantern.com
      </li>
    </ul>
  </section>

  <section class="card card-back" aria-label="Card back">
    <div class="back-band top"></div>
    <h2 class="appointment-title">Appointment</h2>
    <p class="field name">Name :<span class="field-line"></span></p>
    <p class="field date">Date :<span class="field-line"></span></p>
    <p class="notice">If unable to keep appointment, kindly give 24hrs notice.</p>
    <div class="back-band bottom"></div>
  </section>

</main>
</body>
</html>
```